Holiday Graphic for Cover of Catalog

We're looking for a design that represents the Holiday season to use on the cover of this year's holiday catalog. You can take a look at 2011's catalog at this link: http://pagevault.example/brindlewick/docs/holiday_gift_guide. Your design should not be a replication, but it can be inspired by the cover of 2011's Catalog.

Please create a design that is WINTER-specific, not necessarily Christmas, Hanukkah, or any other holiday-specific design. Something simple, modern, contemporary is preferable. The design should have a specific color scheme & that scheme should be easily detectable by a viewer.

Options for The final size of the front-cover:
a. 8.5"width x 5.405"height
b. 8.5"width x 10.81"height
c. 10.81"height x 8.5"width
d. square 8.5" x 8.5"
Updates

Please note: I do not have the time or budget to have these printed with foil stamping, so please avoid any metallic finishes.  

Thanks!
Lena

Requirements
Must have
• Our logo, attached file.
• Title: "2013 Holiday Gift Giving Guide"

```html
<!DOCTYPE html>
<html lang="en">
<head>
<meta charset="utf-8">
<title>2013 Holiday Gift Giving Guide — Catalog Cover</title>
<link rel="stylesheet" href="https://fonts.googleapis.com/css2?family=Damion&family=Montserrat:wght@700&display=swap">
<style>
  :root {
    --paper: #ffffff;
    --frame-line: #c9c9c9;
    --sky-top: #25367a;
    --sky-low: #22346c;
    --mountain: #1f3160;
    --hill-back: #75819a;
    --hill-front: #d2dae6;
    --title-white: #ffffff;
    --title-shadow: #9aa0ab;
    --brand-accent: #f7b52c;
    --brand-ink: #1d1d1d;
  }
  * { margin: 0; padding: 0; box-sizing: border-box; }
  html, body {
    width: 1200px;
    height: 1200px;
    overflow: hidden;
    background: var(--paper);
  }
  .cover {
    position: relative;
    width: 1200px;
    height: 1200px;
    background: var(--paper);
  }
  .cover__art {
    position: absolute;
    left: 16px;
    top: 16px;
    width: 1168px;
    height: 1168px;
    border: 1px solid var(--frame-line);
    overflow: hidden;
  }
  .cover__scene {
    position: absolute;
    inset: 0;
    background: linear-gradient(180deg, var(--sky-top) 0%, var(--sky-low) 22%, var(--mountain) 40%, var(--mountain) 100%);
  }
  .cover__ground {
    position: absolute;
    left: 0;
    bottom: 0;
    width: 100%;
    height: 240px;
  }
  .title {
    position: absolute;
    left: 0;
    top: 440px;
    width: 1200px;
    height: 380px;
    transform: rotate(-2.5deg);
    transform-origin: 610px 190px;
    color: var(--title-white);
    text-align: center;
  }
  .title__year {
    position: absolute;
    left: 0;
    top: 22px;
    width: 1220px;
    font-family: 'Montserrat', Arial, sans-serif;
    font-weight: 700;
    font-size: 62px;
    line-height: 1;
    letter-spacing: 1px;
    text-shadow: 4px 4px 0 var(--title-shadow);
  }
  .title__rule {
    position: absolute;
    height: 5px;
    background: var(--title-white);
  }
  .title__rule--left  { left: 330px; top: 62px; width: 178px; }
  .title__rule--right { left: 712px; top: 62px; width: 178px; }
  .title__rule--bottom { left: 340px; top: 338px; width: 576px; }
  .title__word {
    position: absolute;
    left: 0;
    top: 54px;
    width: 1220px;
    font-family: 'Damion', cursive;
    font-size: 210px;
    line-height: 1;
    text-shadow: 9px 8px 0 var(--title-shadow);
  }
  .title__sub {
    position: absolute;
    left: 0;
    top: 272px;
    width: 1220px;
    font-family: 'Montserrat', Arial, sans-serif;
    font-weight: 700;
    font-size: 38px;
    line-height: 1;
    text-shadow: 3px 3px 0 var(--title-shadow);
  }
  .brand {
    position: absolute;
    right: 62px;
    bottom: 70px;
    display: flex;
    align-items: center;
    gap: 12px;
  }
  .brand__dot {
    width: 40px;
    height: 40px;
    border-radius: 50%;
    background: var(--brand-accent);
  }
  .brand__name {
    font-family: 'Montserrat', Arial, sans-serif;
    font-weight: 700;
    font-size: 24px;
    letter-spacing: 1px;
    color: var(--brand-ink);
  }
</style>
</head>
<body>
  <main class="cover">
    <div class="cover__art">
      <div class="cover__scene" role="img" aria-label="Illustrated snowy night: falling snow over layered navy and grey mountains, with small white-capped trees on the hills"></div>
      <svg class="cover__ground" viewBox="0 0 1168 240" preserveAspectRatio="none" aria-hidden="true">
        <path class="ground__back" d="M0 16 C 200 0, 420 20, 620 36 C 800 50, 980 26, 1168 46 L1168 240 L0 240 Z" fill="var(--hill-back)"/>
        <path class="ground__front" d="M0 160 C 150 140, 300 135, 480 140 C 700 146, 880 60, 1168 74 L1168 240 L0 240 Z" fill="var(--hill-front)"/>
      </svg>
    </div>

    <section class="title" aria-label="2013 Holiday Gift Giving Guide">
      <span class="title__rule title__rule--left"></span>
      <h2 class="title__year">2013</h2>
      <span class="title__rule title__rule--right"></span>
      <h1 class="title__word">Holiday</h1>
      <p class="title__sub">GIFT GIVING GUIDE</p>
      <span class="title__rule title__rule--bottom"></span>
    </section>

    <div class="brand">
      <span class="brand__dot"></span>
      <span class="brand__name">BRINDLEWICK</span>
    </div>
  </main>
</body>
</html>
```